Moxy Fen needs some awesome stationary

Do you have what it takes to get my brand? You either do or you don't, have a crack at a design and you my just win my business.

I don't want to waste your or my time, so put your creative genius on either a business card or envelope.

I however need a package of stationary that follows the same brand. I will message you to complete the remaining should I like your first submission.

Here is what I need, have a go!

Basically I need the following for my small business based in melbourne.
- Letterhead (printer ready and MS Word)
- Business Card
- Compliments Slip
- Envelope
- Proposal Cover Page (MS Word only)
- Presentation Folder
- Marbled Fox Cards
- Student Name Tent
- Index Cards
- Vell-Ka

I am establishing the brand and it must be modern, professional but also relaxed; that is not formal and not corporate. It represents a company are leaders, but small enough to care and operate like a bunch of friends. We are bringing people and conversations back to business, and turfing out all the bureaucracy and crazy and wasteful procedures. Its about "lets talk and figure it out together and find even better ways".

Target Market(s)

Mainly companies that build software products, but Agile practices are used in many other industries (even graphic design projects)

Industry/Entity Type

Information Technology

Font styles to use
Sans Serif

Colors
3176b5
aaaaaa

Requirements
Must have
• I like curves and circles and not boxes or rectangles.
• I want a colour rich design with my brand colours, but it must be balanced.
• I want more modern than traditional, but simple modern
Should not have
• Not corporate
• Please don't waste my time if your not going to think about it.
• Don't mess with my primary logo
• Don't change my colours
• Don't overlay logo on image

```html
<!DOCTYPE html>
<html lang="en">
<head>
<meta charset="utf-8">
<title>Moxy Fen — Index Cards</title>
<link rel="stylesheet" href="https://fonts.googleapis.com/css2?family=Roboto+Condensed:wght@700&display=swap">
<style>
  :root {
    --backdrop: #3a9fd9;
    --card: #ffffff;
    --rule: #e6e6e6;
    --navy: #2e3192;
    --brand-blue: #1f4fa3;
    --accent-blue: #2e3192;
    --accent-red: #ed1c24;
    --accent-green: #00a651;
    --accent-yellow: #fff200;
    --accent-magenta: #ec008c;
  }
  html, body {
    margin: 0;
    width: 1200px;
    height: 960px;
    overflow: hidden;
    background: var(--backdrop);
    font-family: "Roboto Condensed", "Arial Narrow", sans-serif;
  }
  .sheet {
    position: relative;
    width: 1200px;
    height: 960px;
  }
  .index-card {
    position: absolute;
    background: var(--card);
    box-shadow: 6px 7px 6px rgba(20, 60, 100, 0.45);
    overflow: hidden;
  }
  .index-card--blue    { left: 37px;  top: 33px;  width: 356px; height: 423px; --accent: var(--accent-blue); }
  .index-card--red     { left: 423px; top: 33px;  width: 350px; height: 416px; --accent: var(--accent-red); }
  .index-card--green   { left: 811px; top: 33px;  width: 358px; height: 425px; --accent: var(--accent-green); }
  .index-card--yellow  { left: 175px; top: 502px; width: 357px; height: 423px; --accent: var(--accent-yellow); }
  .index-card--magenta { left: 667px; top: 506px; width: 362px; height: 430px; --accent: var(--accent-magenta); }

  .header-rule {
    position: absolute;
    left: 0; right: 0;
    top: 13.6%;
    height: 4px;
    background: var(--accent);
  }
  .writing-line {
    position: absolute;
    left: 0; right: 0;
    height: 1px;
    background: var(--rule);
  }
  .writing-line:nth-of-type(2) { top: 22.9%; }
  .writing-line:nth-of-type(3) { top: 32.8%; }
  .writing-line:nth-of-type(4) { top: 42.7%; }
  .writing-line:nth-of-type(5) { top: 52.6%; }
  .writing-line:nth-of-type(6) { top: 62.5%; }
  .writing-line:nth-of-type(7) { top: 72.4%; }
  .footer-rule {
    position: absolute;
    left: 0; right: 0;
    top: 82%;
    height: 2px;
    background: var(--navy);
  }
  .brand {
    position: absolute;
    left: 17px;
    bottom: 10px;
    display: flex;
    flex-direction: column;
    align-items: center;
    gap: 3px;
  }
  .brand-dot {
    width: 26px;
    height: 26px;
    border-radius: 50%;
    background: var(--brand-blue);
  }
  .brand-name {
    font-size: 10px;
    color: var(--brand-blue);
    letter-spacing: 0.2px;
  }
  .company-name {
    position: absolute;
    left: 51%;
    bottom: 12px;
    transform: translateX(-50%);
    font-size: 10px;
    color: var(--brand-blue);
    white-space: nowrap;
  }
  .tick-circle {
    position: absolute;
    right: 10px;
    bottom: 9px;
    width: 57px;
    height: 57px;
    border: 2px solid var(--brand-blue);
    border-radius: 50%;
  }
</style>
</head>
<body>
<main class="sheet">
  <article class="index-card index-card--blue">
    <div class="header-rule"></div>
    <div class="writing-line"></div><div class="writing-line"></div><div class="writing-line"></div>
    <div class="writing-line"></div><div class="writing-line"></div><div class="writing-line"></div>
    <div class="footer-rule"></div>
    <div class="brand"><span class="brand-dot"></span><span class="brand-name">Moxy Fen</span></div>
    <div class="company-name">Moxy Fen Pty Ltd</div>
    <div class="tick-circle"></div>
  </article>

  <article class="index-card index-card--red">
    <div class="header-rule"></div>
    <div class="writing-line"></div><div class="writing-line"></div><div class="writing-line"></div>
    <div class="writing-line"></div><div class="writing-line"></div><div class="writing-line"></div>
    <div class="footer-rule"></div>
    <div class="brand"><span class="brand-dot"></span><span class="brand-name">Moxy Fen</span></div>
    <div class="company-name">Moxy Fen Pty Ltd</div>
    <div class="tick-circle"></div>
  </article>

  <article class="index-card index-card--green">
    <div class="header-rule"></div>
    <div class="writing-line"></div><div class="writing-line"></div><div class="writing-line"></div>
    <div class="writing-line"></div><div class="writing-line"></div><div class="writing-line"></div>
    <div class="footer-rule"></div>
    <div class="brand"><span class="brand-dot"></span><span class="brand-name">Moxy Fen</span></div>
    <div class="company-name">Moxy Fen Pty Ltd</div>
    <div class="tick-circle"></div>
  </article>

  <article class="index-card index-card--yellow">
    <div class="header-rule"></div>
    <div class="writing-line"></div><div class="writing-line"></div><div class="writing-line"></div>
    <div class="writing-line"></div><div class="writing-line"></div><div class="writing-line"></div>
    <div class="footer-rule"></div>
    <div class="brand"><span class="brand-dot"></span><span class="brand-name">Moxy Fen</span></div>
    <div class="company-name">Moxy Fen Pty Ltd</div>
    <div class="tick-circle"></div>
  </article>

  <article class="index-card index-card--magenta">
    <div class="header-rule"></div>
    <div class="writing-line"></div><div class="writing-line"></div><div class="writing-line"></div>
    <div class="writing-line"></div><div class="writing-line"></div><div class="writing-line"></div>
    <div class="footer-rule"></div>
    <div class="brand"><span class="brand-dot"></span><span class="brand-name">Moxy Fen</span></div>
    <div class="company-name">Moxy Fen Pty Ltd</div>
    <div class="tick-circle"></div>
  </article>
</main>
</body>
</html>
```